Theme and starter template for small business powerpoint deck

We are starting a technology consulting company and would like to have a powerpoint/google slide theme and initial template. We are more concerned with the theme/colors at this point. Initial template can be pretty simple. We would want a cover slide, agenda slide, some content slides including text content, image content, a combination of both, etc. A closing slide. we have included jpg files of our logo, let us know if you would prefer eps/vector. I assume you may want exact color data as well?

Target Market(s)

Technology and Customer Experience Leadership at companies with 25 or more employees

Industry/Entity Type

Technology Consulting

Font styles to use
Sans Serif

Colors
0054AA
0677BA
7BADD7
CADEEF
E8F1F8

Requirements
Must have
• I have attached JPG and EPS and vector files to project. I would like to stay with those colors but open to slight variation if recommended.

```html
<!DOCTYPE html>
<html lang="en">
<head>
<meta charset="utf-8">
<title>Vantrel – Presentation Theme</title>
<link rel="stylesheet" href="https://fonts.googleapis.com/css2?family=Poppins:wght@400;500;600;700&display=swap">
<style>
  :root{
    --canvas:#545454;
    --navy:#0054AA;
    --azure:#0677BA;
    --sky:#7BADD7;
    --pale:#CADEEF;
    --mist:#E8F1F8;
    --ink:#1d1d28;
    --muted:#55586a;
    --rule:#b9bac2;
    --paper:#ffffff;
  }
  *{box-sizing:border-box;margin:0;padding:0}
  html,body{width:1019px;height:1200px;overflow:hidden;background:var(--canvas)}
  body{position:relative;font-family:"Poppins",Arial,sans-serif;color:var(--ink)}
  .slide{position:absolute;width:479px;height:269px;background:var(--paper);overflow:hidden}
  .col-l{left:18px}.col-r{left:521px}
  .row-1{top:16px}.row-2{top:311px}.row-3{top:611px}.row-4{top:910px}
  .abs{position:absolute}
  .wordmark{position:absolute;top:11px;right:15px;font-weight:700;font-size:10.5px;letter-spacing:.6px;color:var(--ink);display:flex;align-items:center;gap:3px;border-bottom:1px solid var(--rule);padding-bottom:1px;line-height:1}
  .wordmark i{display:block;width:5px;height:5px;background:var(--navy)}
  .marker{position:absolute;left:0;width:0;height:0;border-top:11px solid transparent;border-bottom:11px solid transparent;border-left:16px solid var(--navy)}
  .title{position:absolute;left:31px;font-weight:600;font-size:15.5px;line-height:1.2;border-bottom:1.2px solid var(--rule);padding-bottom:2px}
  .footer{position:absolute;left:17px;right:27px;bottom:11px;font-size:5.2px;color:var(--ink);display:flex;justify-content:space-between}
  .band{position:absolute;left:0;right:0;bottom:0;height:3px;background:linear-gradient(90deg,var(--navy) 82.5%,var(--sky) 82.5%)}
  .body-text{font-size:8.1px;line-height:12.4px;color:var(--muted)}
  .socials{display:flex;gap:3px}
  .socials span{width:14px;height:14px;border-radius:50%;border:1px solid var(--navy)}
  /* cover */
  .cover{background:linear-gradient(120deg,var(--pale) 0%,var(--mist) 45%,#fff 75%)}
  .cover .brand{left:26px;top:58px;font-weight:700;font-size:20px;letter-spacing:1.2px;border-bottom:2px solid var(--rule);line-height:1.05;display:flex;align-items:center;gap:5px}
  .cover .brand i{display:block;width:8px;height:8px;background:var(--navy)}
  .cover .welcome{left:27px;top:107px;font-size:16px;color:#1f2a4a}
  .cover .name{left:26px;top:127px;font-size:27px;font-weight:700;color:var(--navy);letter-spacing:.5px}
  .cover .tag{left:27px;top:168px;font-size:13px;color:var(--ink)}
  .cover .socials{left:26px;top:241px}
  /* services */
  .card{position:absolute;top:83px;width:129px;height:118px;background:#fff;box-shadow:0 1px 4px rgba(0,0,0,.14)}
  .card .ph{position:absolute;left:0;top:0;width:129px;height:94px}
  .card .lbl{position:absolute;left:15px;bottom:8px;font-size:7.5px}
  .card svg.go{position:absolute;right:6px;bottom:7px}
  /* agenda */
  .agenda-list{position:absolute;left:237px;top:76px;width:171px;list-style:none}
  .agenda-list li{display:flex;height:19.5px;align-items:center;border-bottom:.6px solid #d6d7dd;font-size:8.6px}
  .agenda-list b{width:30px;padding-left:10px;color:var(--azure);font-weight:400}
  /* consulting */
  .hero{left:0;top:0;width:479px;height:134px;background:linear-gradient(100deg,var(--navy) 0%,var(--azure) 65%,var(--navy) 100%)}
  .consult{background:var(--mist)}
  .consult .ttl{left:31px;top:86px;font-size:15.5px;font-weight:600;color:#fff;border-bottom:1.2px solid #fff;padding-bottom:1px}
  .box{position:absolute;width:220px;height:61px;border-radius:5px;padding:9px 12px}
  .box h4{font-size:6.2px;font-weight:600;margin-bottom:3px}
  .box p{font-size:3.6px;line-height:7px}
  .box.light{left:228px;top:79px;background:#fff;box-shadow:0 1px 4px rgba(0,0,0,.12)}
  .box.light p{color:var(--muted)}
  .box.accent{left:240px;top:154px;background:var(--azure);color:#fff}
  /* team */
  .member{position:absolute;top:66px;width:94px;text-align:center}
  .member .ph{width:94px;height:86px}
  .member .nm{margin:0 -2px;height:17px;line-height:17px;background:#fff;box-shadow:0 1px 3px rgba(0,0,0,.14);font-size:7.3px;font-weight:500;color:var(--navy)}
  .member p{margin-top:13px;font-size:4.3px;line-height:7.5px;color:var(--muted);padding:0 3px}
  .member .socials{justify-content:center;gap:5px;margin-top:6px}
  .member .socials span{width:15px;height:15px;border-color:var(--azure)}
  /* thanks */
  .thanks .brand{left:34px;top:50px;display:flex;align-items:center;gap:4px;font-weight:700;font-size:9px;letter-spacing:.6px}
  .thanks .brand i{display:block;width:14px;height:14px;background:var(--navy)}
  .thanks .ty{left:7px;top:86px;display:flex;align-items:center;gap:5px;font-size:17px;font-weight:600;color:var(--navy)}
  .thanks .ty::before,.thanks .ty::after{content:"";width:18px;height:1px;background:var(--navy)}
  .thanks .pn{left:40px;top:133px;font-size:8px;font-weight:500;color:#333}
  .contact{position:absolute;left:39px;list-style:none;font-size:5.3px;color:#444}
  .contact li{display:flex;align-items:flex-start;gap:6px;height:17px}
  .contact svg{flex:none}
</style>
</head>
<body>

<!-- 1. Cover -->
<section class="slide col-l row-1 cover">
  <div class="abs brand">VANTREL<i></i></div>
  <div class="abs welcome">WELCOME TO</div>
  <div class="abs name">VANTREL</div>
  <div class="abs tag">Technology Consulting</div>
  <div class="abs" style="left:0;top:140px;width:0;height:0;border-top:12px solid transparent;border-bottom:12px solid transparent;border-left:16px solid var(--azure)"></div>
  <div class="abs socials"><span></span><span></span><span></span><span></span></div>
  <svg class="abs" style="left:0;top:0" width="479" height="269">
    <defs>
      <linearGradient id="photoA" x1="0" y1="0" x2="1" y2="1"><stop offset="0" stop-color="#3b5b7c"/><stop offset="1" stop-color="#1f2d3d"/></linearGradient>
      <linearGradient id="photoB" x1="0" y1="0" x2="1" y2="1"><stop offset="0" stop-color="#6f8cb0"/><stop offset="1" stop-color="#2d3d55"/></linearGradient>
      <linearGradient id="photoC" x1="0" y1="0" x2="1" y2="1"><stop offset="0" stop-color="#c9a48a"/><stop offset="1" stop-color="#3a2e2a"/></linearGradient>
    </defs>
    <polygon points="346,91 463,91 405,0" fill="var(--navy)"/>
    <polygon points="288,191 405,191 346,91" fill="url(#photoA)" role="img" aria-label="Photo of consultants reviewing work in an office"/>
    <polygon points="346,91 463,91 405,191" fill="#fff"/>
    <polygon points="405,191 463,91 479,91 479,191" fill="url(#photoB)" role="img" aria-label="Photo of a team working at laptops"/>
    <polygon points="405,191 479,191 479,269 450,269" fill="var(--azure)"/>
    <polygon points="360,269 405,191 450,269" fill="url(#photoC)" role="img" aria-label="Photo of colleagues collaborating at a desk"/>
  </svg>
</section>

<!-- 2. Our Services -->
<section class="slide col-r row-1">
  <div class="marker" style="top:18px"></div>
  <h2 class="title" style="top:16px">Our Services</h2>
  <div class="wordmark">VANTREL<i></i></div>
  <div class="card" style="left:23px">
    <div class="ph" role="img" aria-label="Photo of engineers with a laptop in a server room" style="background:linear-gradient(135deg,#3c4b5c,#17212c)"></div>
    <span class="lbl">Lorem Ipsum</span>
    <svg class="go" width="26" height="22" viewBox="0 0 26 22"><polygon points="13,0 26,22 0,22" fill="var(--navy)"/><path d="M8 15h10M14 11l4 4-4 4" stroke="#fff" stroke-width="1.6" fill="none"/></svg>
  </div>
  <div class="card" style="left:173px">
    <div class="ph" role="img" aria-label="Photo of a professional working at a desk" style="background:linear-gradient(135deg,#2f3d6a,#6a5a7c)"></div>
    <span class="lbl">Lorem Ipsum</span>
    <svg class="go" width="26" height="22" viewBox="0 0 26 22"><polygon points="13,0 26,22 0,22" fill="var(--azure)"/><path d="M8 15h10M14 11l4 4-4 4" stroke="#fff" stroke-width="1.6" fill="none"/></svg>
  </div>
  <div class="card" style="left:323px">
    <div class="ph" role="img" aria-label="Photo of hands on a laptop with digital light effects" style="background:linear-gradient(135deg,#28324a,#0f1626)"></div>
    <span class="lbl">Lorem Ipsum</span>
    <svg class="go" width="26" height="22" viewBox="0 0 26 22"><polygon points="13,0 26,22 0,22" fill="var(--navy)"/><path d="M8 15h10M14 11l4 4-4 4" stroke="#fff" stroke-width="1.6" fill="none"/></svg>
  </div>
  <div class="footer"><span>©Copyrights 2024 Vantrel &nbsp;|&nbsp;&nbsp; All Rights Reserved</span><span>Page | 05</span></div>
  <div class="band"></div>
</section>

<!-- 3. Agenda -->
<section class="slide col-l row-2" style="background:linear-gradient(120deg,#fff 40%,#eeeff2 100%)">
  <div class="marker" style="top:18px"></div>
  <h2 class="title" style="top:20px;font-size:12.5px">Agenda</h2>
  <div class="wordmark">VANTREL<i></i></div>
  <svg class="abs" style="left:0;top:0" width="230" height="215">
    <polygon points="121,42 73,126 169,126" fill="#55607a" role="img" aria-label="Photo of a desk with laptop and charts"/>
    <polygon points="73,126 25,209 121,209" fill="#5f6a5e" role="img" aria-label="Photo of hands typing on a keyboard"/>
    <polygon points="169,126 121,209 217,209" fill="#c98e86" role="img" aria-label="Photo of a desk with coffee and documents"/>
  </svg>
  <ul class="agenda-list">
    <li><b>i.</b>Introduction</li>
    <li><b>ii.</b>About Us</li>
    <li><b>iii.</b>Welcome Message</li>
    <li><b>iv.</b>Our Services</li>
    <li><b>v.</b>Our Team</li>
    <li><b>vi.</b>Contact Us</li>
  </ul>
  <div class="footer"><span>©Copyrights 2024 Vantrel &nbsp;|&nbsp;&nbsp; All Rights Reserved</span><span>Page | 02</span></div>
  <div class="band"></div>
</section>

<!-- 4. Complete Consulting -->
<section class="slide col-r row-2 consult">
  <div class="abs hero" role="img" aria-label="Blue-tinted photo of a consultant in front of data screens"></div>
  <div class="wordmark" style="color:#fff;border-color:#fff">VANTREL<i style="background:#fff"></i></div>
  <div class="abs" style="left:0;top:87px;width:0;height:0;border-top:12px solid transparent;border-bottom:12px solid transparent;border-left:16px solid #fff"></div>
  <h2 class="abs ttl">Complete Consulting</h2>
  <div class="box light"><h4>Lorem ipsum dolor sit</h4><p>Lorem ipsum dolor sit amet, consectetur adipiscing elit, sed do eiusmod tempor incididunt ut labore et dolore magna aliqua. Ut enim ad minim veniam, quis nostrud exercitation ullamco laboris nisi ut aliquip ex ea commodo consequat.</p></div>
  <p class="abs body-text" style="left:32px;top:155px;width:182px;font-size:7.3px;line-height:13.2px;color:#333">Sed ut perspiciatis unde omnis iste natus error sit voluptatem accusantium doloremque laudan-tium, totam rem aperiam, eaque ipsa quae ab illo inventore veritatis et quasi architecto beatae vitae dicta sunt explicabo.</p>
  <div class="box accent"><h4>Lorem ipsum dolor sit</h4><p>Lorem ipsum dolor sit amet, consectetur adipiscing elit, sed do eiusmod tempor incididunt ut labore et dolore magna aliqua. Ut enim ad minim veniam, quis nostrud exercitation ullamco laboris nisi ut aliquip ex ea commodo consequat.</p></div>
  <svg class="abs" style="left:260px;top:216px" width="80" height="50"><polygon points="40,0 80,50 0,50" fill="var(--pale)"/></svg>
  <div class="footer"><span>©Copyrights 2024 Vantrel &nbsp;|&nbsp;&nbsp; All Rights Reserved</span><span>Page | 06</span></div>
  <div class="band"></div>
</section>

<!-- 5. Welcome Message -->
<section class="slide col-l row-3" style="background:linear-gradient(120deg,#fafafa,#ececee)">
  <svg class="abs" style="left:0;top:0" width="479" height="269">
    <polygon points="0,160 0,249 50,249" fill="var(--pale)"/>
    <polygon points="479,110 400,249 479,249" fill="var(--mist)"/>
  </svg>
  <div class="marker" style="top:19px"></div>
  <h2 class="title" style="top:16px;left:31px">Welcome Message</h2>
  <div class="wordmark">VANTREL<i></i></div>
  <p class="abs body-text" style="left:36px;top:77px;width:190px">Lorem ipsum dolor sit amet, consectetur adipiscing elit, sed do eiusmod tempor incididunt ut labore et dolore magna aliqua. Ut enim ad minim veniam, quis nostrud exercitation ullamco laboris nisi ut aliquip ex ea commodo consequat. Duis aute irure dolor in reprehenderit in voluptate velit esse cillum dolore eu fugiat nulla pariatur. Excepteur sint occaecat cupidatat non proident, sunt in culpa qui officia deserunt mollit anim id est laborum.</p>
  <p class="abs body-text" style="left:254px;top:77px;width:190px">Lorem ipsum dolor sit amet, consectetur adipiscing elit, sed do eiusmod tempor incididunt ut labore et dolore magna aliqua. Ut enim ad minim veniam, quis nostrud exercitation ullamco laboris nisi ut aliquip ex ea commodo consequat. Duis aute irure dolor in reprehenderit in voluptate velit esse cillum dolore eu fugiat nulla pariatur. Excepteur sint occaecat cupidatat non proident, sunt in culpa qui officia deserunt mollit anim id est laborum.</p>
  <div class="footer"><span>©Copyrights 2024 Vantrel &nbsp;|&nbsp;&nbsp; All Rights Reserved</span><span>Page | 03</span></div>
  <div class="band"></div>
</section>

<!-- 6. Our Team -->
<section class="slide col-r row-3">
  <div class="marker" style="top:18px"></div>
  <h2 class="title" style="top:16px">Our Team</h2>
  <div class="wordmark">VANTREL<i></i></div>
  <div class="member" style="left:31px">
    <div class="ph" role="img" aria-label="Portrait of team member" style="background:linear-gradient(160deg,#d9dadc,#8a8c90)"></div>
    <div class="nm">Owen Hale</div>
    <p>Lorem ipsum dolor sit amet, consectetur adipiscing elit, sed do incididunt ut labore et dolore magna aliqua.</p>
    <div class="socials"><span></span><span></span><span></span></div>
  </div>
  <div class="member" style="left:139px">
    <div class="ph" role="img" aria-label="Portrait of team member" style="background:linear-gradient(160deg,#e4e6e8,#6e737a)"></div>
    <div class="nm">Leo Marsh</div>
    <p>Lorem ipsum dolor sit amet, consectetur adipiscing elit, sed do incididunt ut labore et dolore magna aliqua.</p>
    <div class="socials"><span></span><span></span><span></span></div>
  </div>
  <div class="member" style="left:247px">
    <div class="ph" role="img" aria-label="Portrait of team member" style="background:linear-gradient(160deg,#a9c3dc,#3d4656)"></div>
    <div class="nm">Clara Reyes</div>
    <p>Lorem ipsum dolor sit amet, consectetur adipiscing elit, sed do incididunt ut labore et dolore magna aliqua.</p>
    <div class="socials"><span></span><span></span><span></span></div>
  </div>
  <div class="member" style="left:355px">
    <div class="ph" role="img" aria-label="Portrait of team member" style="background:linear-gradient(160deg,#cfcac4,#8c7e70)"></div>
    <div class="nm">Miles Carter</div>
    <p>Lorem ipsum dolor sit amet, consectetur adipiscing elit, sed do incididunt ut labore et dolore magna aliqua.</p>
    <div class="socials"><span></span><span></span><span></span></div>
  </div>
  <div class="footer"><span>©Copyrights 2024 Vantrel &nbsp;|&nbsp;&nbsp; All Rights Reserved</span><span>Page | 07</span></div>
  <div class="band"></div>
</section>

<!-- 7. About Us -->
<section class="slide col-l row-4" style="background:linear-gradient(120deg,#f4f6fa,#fff 60%)">
  <svg class="abs" style="left:0;top:0" width="479" height="269">
    <polygon points="479,0 479,100 430,100" fill="var(--pale)"/>
    <polygon points="479,150 479,249 410,249" fill="var(--mist)"/>
    <polygon points="254,223 265,223 338,58 327,58" fill="var(--azure)"/>
    <polygon points="265,223 465,223 465,58 338,58" fill="#2c3a52" role="img" aria-label="Photo of two engineers with a laptop in a data centre"/>
  </svg>
  <div class="marker" style="top:18px"></div>
  <h2 class="title" style="top:16px;border:0">About Us</h2>
  <div class="wordmark">VANTREL<i></i></div>
  <p class="abs body-text" style="left:36px;top:77px;width:190px">Lorem ipsum dolor sit amet, consectetur adipiscing elit, sed do eiusmod tempor incididunt ut labore et dolore magna aliqua. Ut enim ad minim veniam, quis nostrud exercitation ullamco laboris nisi ut aliquip ex ea commodo consequat. Duis aute irure dolor in reprehenderit in voluptate velit esse cillum dolore eu fugiat nulla pariatur. Excepteur sint occaecat cupidatat non proident, sunt in culpa qui officia deserunt mollit anim id est laborum.</p>
  <div class="footer"><span>©Copyrights 2024 Vantrel &nbsp;|&nbsp;&nbsp; All Rights Reserved</span><span>Page | 04</span></div>
  <div class="band"></div>
</section>

<!-- 8. Thank You -->
<section class="slide col-r row-4 thanks">
  <svg class="abs" style="left:0;top:0" width="479" height="269">
    <polygon points="230,0 479,0 479,269 225,269 300,135" fill="#6d7480" role="img" aria-label="Photo of a business team meeting around a table"/>
    <polygon points="300,135 225,269 135,269 253,216" fill="var(--canvas)"/>
    <polygon points="129,0 230,0 300,135 253,216" fill="var(--azure)"/>
  </svg>
  <div class="abs brand"><i></i>VANTREL</div>
  <div class="abs ty">THANK YOU</div>
  <div class="abs pn">PRESENTER NAME</div>
  <ul class="contact" style="top:154px">
    <li><svg width="7" height="7" viewBox="0 0 24 24"><path d="M6.6 10.8a15 15 0 006.6 6.6l2.2-2.2a1 1 0 011-.25 11 11 0 003.6.6 1 1 0 011 1V20a1 1 0 01-1 1A17 17 0 013 4a1 1 0 011-1h3.5a1 1 0 011 1 11 11 0 00.6 3.6 1 1 0 01-.25 1z" fill="var(--azure)"/></svg>(555) 014 2290</li>
    <li><svg width="7" height="7" viewBox="0 0 24 24"><circle cx="12" cy="12" r="10" fill="none" stroke="var(--azure)" stroke-width="3"/><path d="M2 12h20M12 2c3 3 3 17 0 20M12 2c-3 3-3 17 0 20" stroke="var(--azure)" stroke-width="2" fill="none"/></svg>www.vantrel-consult.com</li>
    <li><svg width="7" height="7" viewBox="0 0 24 24"><rect x="2" y="5" width="20" height="14" fill="var(--azure)"/><path d="M2 5l10 8 10-8" stroke="#fff" stroke-width="2" fill="none"/></svg>hello@vantrel-consult.com</li>
    <li><svg width="7" height="8" viewBox="0 0 24 28"><path d="M12 0a9 9 0 00-9 9c0 7 9 19 9 19s9-12 9-19a9 9 0 00-9-9z" fill="var(--azure)"/><circle cx="12" cy="9" r="3.5" fill="#fff"/></svg><span>123 Lorem ipsum dolor sit amet, consectetur<br>adipiscing elit</span></li>
  </ul>
</section>

</body>
</html>
```